create making it look fantastic

create a name for this product and redesign this quick brochure i put together
GLINT ROVER can not be used as it is already trademarked the word rover

```html
<!DOCTYPE html>
<html lang="en">
<head>
<meta charset="utf-8">
<title>Glint Guard – 8-Hour Guard Flyer</title>
<link href="https://fonts.googleapis.com/css2?family=Poppins:wght@300;400;600;700;800&family=Bebas+Neue&family=Oswald:wght@600;700&display=swap" rel="stylesheet">
<style>
  :root{
    --navy:#262063;
    --blue:#2b9ad9;
    --blue-light:#3fa9e6;
    --heading:#2f2474;
    --red:#e5171b;
    --row:#ecebee;
    --ink:#2b2b33;
    --paper:#ffffff;
    --stage:#ffffff;
  }
  *{box-sizing:border-box;margin:0;padding:0}
  html,body{width:1200px;height:2403px;overflow:hidden;background:var(--stage)}
  body{font-family:"Poppins",sans-serif;position:relative}
  .flyer{
    position:absolute;left:54px;top:473px;width:993px;height:1325px;
    transform:scale(1.1);transform-origin:0 0;
    background:var(--paper);overflow:hidden;
  }
  .flyer-bg{position:absolute;inset:0;width:993px;height:1325px}
  .abs{position:absolute;white-space:nowrap}

  .brand-name{left:48px;top:84px;color:#fff;font-weight:700;font-size:50px;letter-spacing:2px;line-height:1}
  .headline-main{left:47px;top:180px;font-family:"Bebas Neue",sans-serif;font-weight:400;font-size:90px;line-height:1;color:var(--blue-light);letter-spacing:0}
  .headline-sub{left:48px;top:262px;font-weight:800;font-size:52px;line-height:1;color:#fff}
  .headline-tail{left:50px;top:322px;font-weight:300;font-size:40px;line-height:1;color:#fff;letter-spacing:12px}

  .product-tag{left:648px;top:60px;height:46px;width:295px;background:var(--blue);border-radius:5px;color:#fff;font-weight:700;font-size:27px;letter-spacing:3px;display:flex;align-items:center;padding-left:45px}
  .product-tag .clock{position:absolute;left:-14px;top:3px;width:40px;height:40px;border-radius:50%;background:#fff;border:3px solid var(--navy)}
  .product-tag .clock::before{content:"";position:absolute;left:16px;top:6px;width:3px;height:13px;background:var(--navy)}
  .product-tag .clock::after{content:"";position:absolute;left:17px;top:17px;width:10px;height:3px;background:var(--navy)}

  .product-photo{left:430px;top:100px;width:540px;height:420px}

  .section-title{font-weight:700;line-height:1}
  .application-title{left:47px;top:452px;color:#fff;font-size:33px}
  .application-list{left:47px;top:500px;width:590px;list-style:none;color:#fff;font-size:18.5px;line-height:22px;white-space:normal}
  .application-list li{position:relative;padding-left:30px;margin-bottom:22px}
  .application-list li::before{content:"";position:absolute;left:0;top:4px;width:15px;height:15px;border-radius:50%;background:var(--navy)}
  .application-list li::after{content:"";position:absolute;left:4px;top:7px;width:6px;height:3px;border-left:2px solid #fff;border-bottom:2px solid #fff;transform:rotate(-45deg)}

  .new-seal{left:662px;top:452px;width:225px;height:225px}
  .new-seal-text{left:662px;top:518px;width:225px;text-align:center;color:#fff;font-weight:700;line-height:1}
  .new-seal-text .big{display:block;font-size:58px;letter-spacing:1px}
  .new-seal-text .small{display:block;font-size:21px;font-weight:600;line-height:22px;margin-top:4px}

  .specs-title{left:550px;top:700px;width:395px;text-align:center;color:var(--heading);font-size:34px}
  .specs-table{left:550px;top:753px;width:395px;font-size:17.5px;color:var(--ink);text-align:center;white-space:normal}
  .specs-table .row{padding:10.5px 8px;line-height:21px;border-radius:10px}
  .specs-table .row:nth-child(odd){background:var(--row)}

  .features-title{left:47px;top:780px;color:var(--heading);font-size:33px}
  .features-list{left:47px;top:822px;width:465px;list-style:none;font-size:18.5px;line-height:21px;color:var(--ink);white-space:normal}
  .features-list li{position:relative;padding-left:53px;margin-bottom:20px}
  .features-list li .icon{position:absolute;left:0;top:2px;width:38px;height:38px;border-radius:50%;background:var(--blue);border:3px solid #cfe4f3}
  .features-list li .icon::after{content:"";position:absolute;left:9px;top:9px;width:14px;height:14px;border-radius:50%;border:2px solid #fff}
  .features-list .fire{color:var(--red);font-weight:600}

  .contact-title{left:47px;top:1177px;color:var(--heading);font-size:33px}

  .danger-plate{left:563px;top:1092px;width:372px;height:150px}
  .danger-text{left:713px;top:1108px;color:var(--navy);line-height:1}
  .danger-text .l1{display:block;font-family:"Oswald",sans-serif;font-weight:700;font-size:29px}
  .danger-text .l2{display:block;font-weight:800;font-size:30px}
  .danger-text .l3{display:block;font-weight:600;font-size:18px;line-height:20px;margin-top:2px}
  .danger-label{left:578px;top:1205px;width:120px;text-align:center;color:#fff;font-family:"Oswald",sans-serif;font-weight:700;font-size:16px}

  .phone{left:48px;top:1240px;color:#fff;font-weight:700;font-size:38px;letter-spacing:3px;display:flex;align-items:center;gap:10px}
  .phone svg{width:32px;height:32px}
  .web-links{left:415px;top:1255px;color:#fff;font-size:18px;display:flex;gap:28px;align-items:center}
  .web-links span{display:flex;align-items:center;gap:8px}
  .web-links svg{width:16px;height:16px}
</style>
</head>
<body>
<main class="flyer">
  <svg class="flyer-bg" viewBox="0 0 993 1325" aria-hidden="true">
    <defs>
      <linearGradient id="navyFade" x1="0" y1="0" x2="1" y2="1">
        <stop offset="0" stop-color="#2a2370"/><stop offset="1" stop-color="#1f1a55"/>
      </linearGradient>
      <linearGradient id="blueFade" x1="0" y1="0" x2="1" y2="0">
        <stop offset="0" stop-color="#2c97d6"/><stop offset="1" stop-color="#1f86cc"/>
      </linearGradient>
      <linearGradient id="plate" x1="0" y1="0" x2="1" y2="1">
        <stop offset="0" stop-color="#eeeff1"/><stop offset=".5" stop-color="#c9cbcf"/><stop offset="1" stop-color="#e3e4e7"/>
      </linearGradient>
    </defs>
    <path d="M0 0H993V150C860 300 620 392 0 410Z" fill="url(#navyFade)"/>
    <path d="M0 419C620 402 870 312 993 165V515C720 690 380 762 0 762Z" fill="url(#blueFade)"/>
    <path d="M0 1222H360Q390 1222 405 1250L445 1325H0Z" fill="var(--navy)"/>
    <path d="M390 1245H993V1325H432Z" fill="var(--blue)"/>
  </svg>

  <div class="abs brand-name">GLINT GUARD</div>
  <div class="abs headline-main">PRIORITIZING</div>
  <div class="abs headline-sub">YOUR SAFETY</div>
  <div class="abs headline-tail">ABOVE ALL</div>

  <div class="abs product-tag"><span class="clock"></span>8-HOUR GUARD</div>

  <svg class="abs product-photo" viewBox="0 0 540 420" role="img" aria-label="Black glass double power outlet with two touch buttons">
    <defs>
      <linearGradient id="glass" x1="0" y1="0" x2="1" y2="1">
        <stop offset="0" stop-color="#3a3a3e"/><stop offset=".55" stop-color="#1b1b1e"/><stop offset="1" stop-color="#0e0e10"/>
      </linearGradient>
    </defs>
    <path d="M16 5L523 80L468 395L16 295Z" fill="url(#glass)"/>
  </svg>

  <h2 class="abs section-title application-title">Application</h2>
  <ul class="abs application-list">
    <li>Our GPO is easily installed by a registered electrician and once it is turned on and customised,<br>it will only operate for up to 8 hours.</li>
    <li>Prevent the risk to your environment of battery operated wheelchairs and scooters.</li>
    <li>The 8-Hour Guard keeps a battery operating equipment safe from overheating and possibly exploding.</li>
  </ul>

  <svg class="abs new-seal" viewBox="0 0 225 225" aria-hidden="true">
    <path fill="var(--red)" d="M112 2l17 13 21-5 10 19 21 3 3 21 19 10-5 21 13 17-13 17 5 21-19 10-3 21-21 3-10 19-21-5-17 13-17-13-21 5-10-19-21-3-3-21-19-10 5-21L2 112l13-17-5-21 19-10 3-21 21-3 10-19 21 5z"/>
  </svg>
  <div class="abs new-seal-text"><span class="big">NEW</span><span class="small">INNOOVATIVE<br>TECHNOLOGY</span></div>

  <h2 class="abs section-title specs-title">Specifications</h2>
  <div class="abs specs-table">
    <div class="row">Colours available with and black.</div>
    <div class="row">Size 120 x 72 x 42mm.</div>
    <div class="row">Capacitive easy touch power on button.</div>
    <div class="row">Operating Voltage: 110-240V</div>
    <div class="row">AC/50Hz-60Hz.</div>
    <div class="row">Rated Current: 10A x 2</div>
    <div class="row">Material: toughened glass panel + fire retardant shell</div>
  </div>

  <h2 class="abs section-title features-title">Features</h2>
  <ul class="abs features-list">
    <li><span class="icon"></span><span class="fire">FIRE</span> retardent double GPO made with V0 material.</li>
    <li><span class="icon"></span>Tempered glass panel easily cleaned and never fades.</li>
    <li><span class="icon"></span>Capacitive easy touch power on button.</li>
    <li><span class="icon"></span>MCU Intelligent Smart Chipset, 3 Year warranty.</li>
    <li><span class="icon"></span>Automatic cut-off of power 2 hours (can be customised).</li>
    <li><span class="icon"></span>Complies with Australian Standards and Approvals.</li>
  </ul>

  <svg class="abs danger-plate" viewBox="0 0 372 150" aria-hidden="true">
    <rect x="120" y="0" width="252" height="150" rx="4" fill="url(#plate)"/>
    <path d="M75 4L148 148H2Z" fill="var(--red)" stroke="#1a1a1a" stroke-width="5" stroke-linejoin="round"/>
  </svg>
  <div class="abs danger-label">DANGER</div>
  <div class="abs danger-text"><span class="l1">RISK OF BATTERY</span><span class="l2">EXPLOSION</span><span class="l3">NO SMOKING<br>SPARKS OF FLAME</span></div>

  <h2 class="abs section-title contact-title">Contact us</h2>
  <div class="abs phone">
    <svg viewBox="0 0 32 32" aria-hidden="true"><circle cx="16" cy="16" r="15" fill="var(--blue-light)"/><path d="M11 8l4 4-2 3q2 4 5 5l3-2 4 4-3 3q-6 0-11-6T8 11z" fill="#fff"/></svg>
    1300 555 018
  </div>
  <div class="abs web-links">
    <span><svg viewBox="0 0 16 16" aria-hidden="true"><path d="M1 8L15 1 11 15 8 10z" fill="var(--navy)"/></svg>info@glintguard.com.au</span>
    <span><svg viewBox="0 0 16 16" aria-hidden="true"><circle cx="8" cy="8" r="7" fill="none" stroke="var(--navy)" stroke-width="2"/><path d="M1 8H15M8 1Q3 8 8 15Q13 8 8 1" fill="none" stroke="var(--navy)" stroke-width="1.5"/></svg>www.glintguard.com.au</span>
  </div>
</main>
</body>
</html>
```